Corvexa Background Design

Need to develop a Corvexa Background picture for my profile. The components I want in there are:
1) Name: Abhrajit Dutta
2) Key Skills: Strategy, Innovation, Execution, Growth and Leadership
3) A photograph (an action photograph) The attached photograph is an example.
A black background would be ideal.

The design should meet the Corvexa background size requirements.

The background should reinforce an image of a thinking person but equally capable of implementing.

Leadership

```html
<!DOCTYPE html>
<html lang="en">
<head>
<meta charset="utf-8">
<title>Abhrajit Dutta – Corvexa Background</title>
<link rel="stylesheet" href="https://fonts.googleapis.com/css2?family=Open+Sans:wght@400;700&display=swap">
<style>
  :root {
    --bg: #000000;
    --accent: #1ea3e0;
    --band-text: #0b1a24;
    --photo-light: #6b6e74;
    --photo-dark: #1c1d20;
  }
  html, body {
    margin: 0;
    padding: 0;
    background: var(--bg);
    overflow: hidden;
  }
  .banner {
    position: relative;
    width: 1200px;
    height: 409px;
    background: var(--bg);
    overflow: hidden;
    font-family: "Open Sans", Arial, sans-serif;
  }
  .portrait {
    position: absolute;
    left: 180px;
    top: 0;
    width: 380px;
    height: 345px;
    background: radial-gradient(ellipse at 55% 40%, var(--photo-light) 0%, #3a3c40 45%, var(--photo-dark) 80%, var(--bg) 100%);
  }
  .name {
    position: absolute;
    left: 14px;
    bottom: 12px;
    margin: 0;
    font-weight: 700;
    font-size: 90px;
    line-height: 1;
    letter-spacing: -1px;
    color: var(--accent);
    white-space: nowrap;
  }
  .name .surname {
    text-transform: uppercase;
  }
  .skills {
    position: absolute;
    left: 829px;
    top: 26px;
    width: 371px;
    margin: 0;
    padding: 0;
    list-style: none;
  }
  .skill {
    position: relative;
    height: 46px;
    margin-bottom: 25px;
    padding-left: 26px;
    font-size: 38px;
    line-height: 44px;
    color: var(--band-text);
  }
  .skill::before {
    content: "";
    position: absolute;
    left: 0;
    top: 0;
    width: 10px;
    height: 100%;
    background: var(--accent);
  }
  .skill::after {
    content: "";
    position: absolute;
    left: 20px;
    right: 0;
    top: 0;
    height: 100%;
    background: var(--accent);
    z-index: -1;
  }
  .skill span {
    position: relative;
  }
  .skills { z-index: 1; isolation: isolate; }
</style>
</head>
<body>
  <div class="banner">
    <div class="portrait" role="img" aria-label="Action photograph of Abhrajit Dutta in a grey blazer, pointing upward"></div>
    <h1 class="name">Abhrajit <span class="surname">Dutta</span></h1>
    <ul class="skills">
      <li class="skill"><span>strategy</span></li>
      <li class="skill"><span>execution</span></li>
      <li class="skill"><span>innovation</span></li>
      <li class="skill"><span>growth</span></li>
      <li class="skill"><span>leadership</span></li>
    </ul>
  </div>
</body>
</html>
```